Website Design for a Project Management Consulting Business

I have a logo design already and now I need a website.
I am a project manager and run my own consulting business.
Currently I am under contract with 3 major Vantage 400 companies. I'd like a website I can direct current and future clients.
My job is running IT projects and working with developers to deliver business priorities.
The website should be professional and clean - I work IT projects and would like to incorporate that into any theme.
I'd like the site to have several page or breakoff links - sections would include : about me, about my services, a page to display all of my certification badges, another page to talk about highlights from past projects and so on.
Looking for a collaborative experience.

Industry/Entity Type

Vantage 400 Consulting Firm - Project Management

Coding

Coded - Design and coding required

Number of Pages Required

1 page

Font styles to use
Serif

Colors
0094D4
00A9DD
6FCCEA
C7EBF8
E9F6FB
EE7325
F08F49
F5BC92
FAE3D3
FDF4ED

Requirements
Must have
• Sections that are a must: About Me (bio), About My Services, About my Certifications and Credentials, Experience on Past Projects,
Nice to have
• I have added the logo below - I'd like to use the logo and have it prominent ; should be professional and inviting

```html
<!DOCTYPE html>
<html lang="en">
<head>
<meta charset="utf-8">
<title>Keystone Delivery, LLC — Project Management Consulting</title>
<link href="https://fonts.googleapis.com/css2?family=Exo+2:wght@600;700;800&family=Montserrat:wght@400;500;600;700&display=swap" rel="stylesheet">
<style>
:root{
  --blue:#0094D4;
  --blue-2:#00A9DD;
  --blue-3:#6FCCEA;
  --blue-4:#C7EBF8;
  --blue-5:#E9F6FB;
  --orange:#EE7325;
  --orange-2:#F08F49;
  --orange-3:#F5BC92;
  --ink:#1f2a36;
  --text:#555c66;
  --grey-bg:#f1f1f1;
  --footer:#121212;
  --white:#ffffff;
}
*{box-sizing:border-box;margin:0;padding:0}
html,body{width:1200px;height:4109px;overflow:hidden}
body{position:relative;background:var(--white);font-family:"Montserrat",sans-serif;color:var(--text)}
.abs{position:absolute}
.heading{font-family:"Exo 2",sans-serif;font-weight:800;color:var(--blue);letter-spacing:.5px;text-transform:uppercase}
.divider{position:absolute;display:flex;align-items:center;gap:14px}
.divider span{display:block;width:72px;height:3px;background:var(--blue)}
.divider i{display:block;width:13px;height:13px;border:2px solid var(--blue)}
.divider.light span{background:#fff}.divider.light i{border-color:#fff}

/* header */
.site-header{position:absolute;left:0;top:0;width:1200px;height:91px;background:#fff}
.brand{position:absolute;display:flex;align-items:center;gap:9px;white-space:nowrap}
.brand b{display:block;width:30px;height:30px;border:3px solid var(--blue);flex:none}
.brand em{font-style:normal;font-family:"Montserrat",sans-serif;font-weight:700;font-size:15.5px;color:#1c3f94;letter-spacing:.5px}
.nav a{position:absolute;top:40px;font-size:12.5px;color:#333;text-decoration:none}
.nav a.active{color:var(--blue)}
.nav .active-bar{position:absolute;left:326px;top:62px;width:34px;height:3px;background:var(--blue)}
.nav .active-icon{position:absolute;left:338px;top:20px;width:14px;height:14px;border:2px solid var(--blue)}
.callnow{left:915px;top:18px;font-size:11px;color:#333}
.callnow strong{font-size:16px;color:#222;margin-left:4px}
.callback{left:915px;top:45px;width:215px;height:28px;background:var(--orange);color:#fff;font-size:12.5px;display:flex;align-items:center;justify-content:center;border-radius:2px}

/* hero */
.hero{position:absolute;left:0;top:91px;width:1200px;height:675px;overflow:hidden}
.hero-photo{position:absolute;inset:0;background:linear-gradient(110deg,#3a9ed8 0%,#1f8fd0 35%,#5b6f86 60%,#8a96a6 80%,#c7ccd4 100%)}
.hero-overlay{position:absolute;inset:0}
.hero-kicker{left:112px;top:212px;font-size:21px;color:#fff;font-weight:500}
.hero-title{left:108px;top:238px;font-family:"Exo 2",sans-serif;font-weight:800;font-size:68px;color:#fff;letter-spacing:1px}
.btn{position:absolute;display:flex;align-items:center;justify-content:space-between;padding:0 12px 0 20px;border-radius:24px;color:#fff;font-weight:700;font-size:13px}
.btn .go{width:30px;height:30px;border-radius:50%;background:#fff;display:flex;align-items:center;justify-content:center}
.btn-orange{background:var(--orange)}
.btn-blue{background:var(--blue)}
.slider-arrow{position:absolute;width:58px;height:58px;border-radius:50%;border:1.5px solid rgba(255,255,255,.8);display:flex;align-items:center;justify-content:center}
.dots{left:574px;top:557px;display:flex;gap:8px;align-items:center}
.dots i{display:block;width:10px;height:10px;border-radius:50%;border:1.5px solid #fff}
.dots i.on{width:15px;height:15px;background:#fff;box-shadow:inset 0 0 0 3px #5b6f86}

/* about */
.about-block{left:0;top:865px;width:303px;height:260px;background:var(--blue)}
.about-photo{left:193px;top:827px;width:254px;height:362px;background:linear-gradient(180deg,#eef0f3,#d9dee5 60%,#7f93b3)}
.about-text p{font-size:13.6px;line-height:25.6px;text-align:justify;color:#444;margin-bottom:16px}

/* services */
.services-bg{left:0;top:1325px;width:1200px;height:702px;background:var(--grey-bg)}
.card{position:absolute;background:#fff;box-shadow:0 6px 14px rgba(0,0,0,.14);border-radius:4px;overflow:hidden}
.service-card{top:1535px;width:308px;height:396px}
.service-card .photo{position:absolute;left:0;top:0;width:100%;height:189px}
.service-card .icon{position:absolute;left:116px;top:147px;width:76px;height:76px;border-radius:50%;background:var(--orange);border:4px solid #fff;display:flex;align-items:center;justify-content:center}
.service-card h3{position:absolute;left:0;right:0;top:231px;text-align:center;font-family:"Exo 2",sans-serif;font-weight:600;font-size:19px;color:#222}
.service-card p{position:absolute;left:22px;right:22px;top:260px;text-align:center;font-size:12.5px;line-height:22.5px;color:#666}
.service-card .more{position:absolute;left:0;right:0;top:360px;display:flex;justify-content:center;align-items:center;gap:18px;font-size:13px;font-style:italic;color:var(--blue);text-decoration:underline}
.more .dot{width:24px;height:24px;border-radius:50%;background:var(--blue);display:flex;align-items:center;justify-content:center}

/* certifications */
.badge{position:absolute;top:2140px;width:106px;height:104px}

/* projects */
.projects-bg{left:0;top:2314px;width:1200px;height:694px;background:var(--blue)}
.project-card{top:2530px;width:308px;height:359px;background:#fff;border-radius:2px}
.project-card .photo{position:absolute;left:7px;top:8px;right:7px;height:255px}
.project-card h3{position:absolute;left:0;right:0;top:291px;text-align:center;font-family:"Exo 2",sans-serif;font-weight:600;font-size:23px;line-height:30px;color:#555;text-transform:uppercase}
.project-card.ghost{background:var(--blue-3)}
.ghost-label{position:absolute;top:2821px;font-family:"Exo 2",sans-serif;font-weight:600;font-size:23px;color:#3a6e8f}
.round-arrow{position:absolute;width:58px;height:58px;border-radius:50%;background:var(--orange);display:flex;align-items:center;justify-content:center}

/* contact */
.dot-field{background:#f7f8f9}
.contact-orange{left:145px;top:3128px;width:334px;height:240px;background:var(--orange);text-align:right;padding:56px 103px 0 0;color:#fff}
.contact-orange small{display:block;font-size:12.5px;font-weight:600;letter-spacing:.5px;margin-bottom:10px}
.contact-orange strong{font-family:"Exo 2",sans-serif;font-weight:800;font-size:30px;line-height:38px;display:block;white-space:nowrap}
.contact-form{left:413px;top:3144px;width:672px;height:463px;background:#fff;box-shadow:0 8px 30px rgba(0,0,0,.12)}
.field{position:absolute;width:256px;border-bottom:1.5px solid #888;padding-bottom:6px}
.field label{display:block;font-size:12.5px;font-weight:600;color:#333;letter-spacing:.4px;margin-bottom:10px}
.field span{font-size:12.5px;color:#888}
.send{position:absolute;left:523px;top:355px;width:66px;height:66px;border-radius:50%;background:var(--orange);box-shadow:0 6px 14px rgba(238,115,37,.4);display:flex;align-items:center;justify-content:center}

/* footer */
.site-footer{left:0;top:3718px;width:1200px;height:391px;background:var(--footer);color:#fff}
.footer-brand{left:112px;top:128px}
.footer-brand b{border-color:#fff}
.footer-brand em{color:#fff}
.fcol{position:absolute;top:92px}
.fcol h4{font-size:15.5px;font-weight:700;margin-bottom:10px}
.fcol h4::after{content:"";display:block;width:50px;height:2px;background:var(--blue);margin-top:10px}
.fcol a{display:block;font-size:13px;line-height:26px;color:#fff;text-decoration:none}
.contact-row{display:flex;gap:10px;margin-bottom:12px}
.contact-row small{display:block;font-size:12px;color:#aaa}
.contact-row span{display:block;font-size:13px;line-height:17px}
.footer-rule{left:112px;top:317px;width:976px;height:1px;background:#444}
.copyright{left:0;width:1200px;top:340px;text-align:center;font-size:16px;color:#eee}
.to-top{left:1121px;top:292px;width:44px;height:44px;border-radius:50%;background:var(--blue);display:flex;align-items:center;justify-content:center}
</style>
</head>
<body>

<header class="site-header">
  <div class="brand" style="left:80px;top:32px"><b></b><em>KEYSTONE DELIVERY</em></div>
  <nav class="nav">
    <i class="active-icon"></i>
    <a href="#" class="active" style="left:326px">Home</a>
    <span class="active-bar"></span>
    <a href="#" style="left:397px">About Me</a>
    <a href="#" style="left:492px">Services</a>
    <a href="#" style="left:579px">Certifications and Credentials</a>
    <a href="#" style="left:788px">Projects</a>
  </nav>
  <div class="abs callnow">Call Now: <strong>+44 207 946 0321</strong></div>
  <div class="abs callback">Request a call back</div>
</header>

<section class="hero">
  <div class="hero-photo" role="img" aria-label="Two business consultants in suits reviewing a clipboard in a bright office"></div>
  <svg class="hero-overlay" width="1200" height="675" viewBox="0 0 1200 675">
    <polygon points="0,0 670,0 420,675 0,675" fill="#1a8fd6" opacity=".55"/>
    <polygon points="0,618 1141,668 1141,675 1200,675 1200,675 0,675" fill="#fff"/>
    <polygon points="0,612 1141,654 1141,670 0,626" fill="var(--orange)"/>
  </svg>
  <div class="abs hero-kicker">PROJECT MANAGEMENT</div>
  <div class="abs hero-title">KEYSTONE</div>
  <div class="btn btn-orange" style="left:112px;top:330px;width:180px;height:45px">GET STARTED
    <span class="go"><svg width="14" height="14" viewBox="0 0 14 14"><path d="M2 7h10M8 3l4 4-4 4" stroke="var(--orange)" stroke-width="1.8" fill="none"/></svg></span></div>
  <div class="slider-arrow" style="left:24px;top:258px"><svg width="18" height="14" viewBox="0 0 18 14"><path d="M16 7H2M7 2L2 7l5 5" stroke="#fff" stroke-width="1.8" fill="none"/></svg></div>
  <div class="slider-arrow" style="left:1117px;top:258px"><svg width="18" height="14" viewBox="0 0 18 14"><path d="M2 7h14M11 2l5 5-5 5" stroke="#fff" stroke-width="1.8" fill="none"/></svg></div>
  <div class="abs dots"><i></i><i class="on"></i><i></i></div>
</section>

<section class="about">
  <div class="abs about-block"></div>
  <div class="abs about-photo" role="img" aria-label="Portrait of Marcus Ellery in a blue checked suit"></div>
  <h2 class="abs heading" style="left:595px;top:822px;font-size:44px">About Me</h2>
  <div class="divider" style="left:595px;top:881px"><span></span><i></i><span></span></div>
  <div class="abs about-text" style="left:595px;top:917px;width:473px">
    <p>Marcus Ellery is the Owner of Keystone Delivery, LLC and serves as Principal Lead Consultant on waterfall and agile contract opportunities.</p>
    <p>Keystone Delivery, LLC has engaged on a contract basis with Vantage 400 companies across various industries including banking and credit unions, global supply chain, and international food distribution. Marcus Ellery brings 12 years of experience to his clients encompassing various project methodologies including: waterfall, agile, and hybrid frameworks.</p>
  </div>
  <div class="btn btn-blue" style="left:594px;top:1183px;width:183px;height:46px">LEARN MORE
    <span class="go"><svg width="14" height="14" viewBox="0 0 14 14"><path d="M2 7h10M8 3l4 4-4 4" stroke="var(--blue)" stroke-width="1.8" fill="none"/></svg></span></div>
</section>

<section class="services">
  <div class="abs services-bg"></div>
  <svg class="abs" style="left:0;top:1318px" width="1200" height="60" viewBox="0 0 1200 60">
    <polygon points="0,0 1200,0 1200,60 0,60" fill="#fff"/>
    <polygon points="0,8 1141,38 1141,60 1200,60 1200,60 0,60" fill="var(--grey-bg)"/>
    <polygon points="0,8 1141,34 1141,48 0,18" fill="var(--orange)"/>
  </svg>
  <h2 class="abs heading" style="left:0;width:1200px;text-align:center;top:1430px;font-size:44px">My Services</h2>
  <div class="divider" style="left:494px;top:1489px"><span></span><i></i><span></span></div>

  <article class="card service-card" style="left:112px">
    <div class="photo" role="img" aria-label="Consultants discussing work at a computer screen" style="background:linear-gradient(135deg,#d9dde2,#8a9099)"></div>
    <div class="icon"><svg width="34" height="34" viewBox="0 0 34 34" fill="none" stroke="#fff" stroke-width="1.8"><circle cx="17" cy="17" r="11"/><path d="M17 10v7l5 3"/></svg></div>
    <h3>Agile Assessment &amp; Roadmap</h3>
    <p>Keystone Advisory Group supports organizations who are ramping up Agile discussions or want to improve their current Agile capabilities.</p>
    <div class="more">Learn More <span class="dot"><svg width="12" height="12" viewBox="0 0 12 12"><path d="M2 6h8M7 3l3 3-3 3" stroke="#fff" stroke-width="1.6" fill="none"/></svg></span></div>
  </article>
  <article class="card service-card" style="left:445px">
    <div class="photo" role="img" aria-label="Team meeting in a glass-walled office" style="background:linear-gradient(135deg,#e4e6e8,#9a9fa6)"></div>
    <div class="icon"><svg width="34" height="34" viewBox="0 0 34 34" fill="none" stroke="#fff" stroke-width="1.8"><circle cx="17" cy="17" r="11"/><circle cx="17" cy="17" r="5"/></svg></div>
    <h3>Agile Transformation</h3>
    <p>Keystone Advisory Group is passionate about the difference high performance agile teams can make.</p>
    <div class="more">Learn More <span class="dot"><svg width="12" height="12" viewBox="0 0 12 12"><path d="M2 6h8M7 3l3 3-3 3" stroke="#fff" stroke-width="1.6" fill="none"/></svg></span></div>
  </article>
  <article class="card service-card" style="left:780px">
    <div class="photo" role="img" aria-label="Two colleagues talking in a modern office" style="background:linear-gradient(135deg,#4a4f57,#9aa0a8)"></div>
    <div class="icon"><svg width="34" height="34" viewBox="0 0 34 34" fill="none" stroke="#fff" stroke-width="1.8"><path d="M17 6l10 6v10l-10 6-10-6V12z"/><path d="M7 12l10 6 10-6M17 18v10"/></svg></div>
    <h3>Agile Scaling</h3>
    <p>Keystone Advisory Group helps companies scale their agile capabilities across multi-team products, platforms, and organizational areas.</p>
    <div class="more">Learn More <span class="dot"><svg width="12" height="12" viewBox="0 0 12 12"><path d="M2 6h8M7 3l3 3-3 3" stroke="#fff" stroke-width="1.6" fill="none"/></svg></span></div>
  </article>
</section>

<section class="certifications">
  <svg class="abs" style="left:0;top:2020px" width="1200" height="60" viewBox="0 0 1200 60">
    <polygon points="0,0 1200,0 1200,60 0,60" fill="#fff"/>
    <polygon points="0,0 1200,0 1200,7 0,7" fill="var(--grey-bg)"/>
    <polygon points="0,4 1141,30 1141,7 1200,7 1200,0 0,0" fill="var(--grey-bg)"/>
    <polygon points="0,4 1141,26 1141,40 0,16" fill="var(--orange)"/>
  </svg>
  <h2 class="abs heading" style="left:112px;top:2160px;font-size:44px">My Certification Badges</h2>
  <div class="divider" style="left:260px;top:2217px"><span></span><i></i><span></span></div>
  <svg class="badge" style="left:710px" viewBox="0 0 106 104" role="img" aria-label="Certification badge"><circle cx="53" cy="52" r="50" fill="#f5b62a"/><circle cx="53" cy="52" r="38" fill="#f0a500"/></svg>
  <svg class="badge" style="left:854px" viewBox="0 0 106 104" role="img" aria-label="Certification badge"><circle cx="53" cy="52" r="50" fill="var(--orange-2)"/><circle cx="53" cy="52" r="38" fill="var(--orange)"/></svg>
  <svg class="badge" style="left:992px" viewBox="0 0 106 104" role="img" aria-label="Certification badge"><circle cx="53" cy="52" r="50" fill="#f5b62a"/><circle cx="53" cy="52" r="38" fill="#f0a500"/></svg>
</section>

<section class="projects">
  <div class="abs projects-bg"></div>
  <svg class="abs" style="left:0;top:2300px" width="1200" height="60" viewBox="0 0 1200 60">
    <polygon points="0,0 1200,0 1200,60 0,60" fill="#fff"/>
    <polygon points="0,14 1141,44 1141,60 1200,60 1200,60 0,60" fill="var(--blue)"/>
    <polygon points="0,10 1141,36 1141,48 0,22" fill="var(--orange)"/>
  </svg>
  <h2 class="abs heading" style="left:0;width:1200px;text-align:center;top:2410px;font-size:44px;color:#fff">Past Projects</h2>
  <div class="divider light" style="left:494px;top:2467px"><span></span><i></i><span></span></div>

  <div class="card project-card ghost" style="left:-232px"></div>
  <div class="ghost-label" style="left:-2px">MENT</div>
  <div class="card project-card ghost" style="left:1112px"></div>
  <div class="ghost-label" style="left:1178px">PI</div>

  <article class="card project-card" style="left:112px">
    <div class="photo" role="img" aria-label="Women arranging sticky notes on a planning wall" style="background:linear-gradient(135deg,#d8b48a,#7a6a5e)"></div>
    <h3>Agile Project<br>Management</h3>
  </article>
  <article class="card project-card" style="left:445px">
    <div class="photo" role="img" aria-label="Team collaborating around a laptop" style="background:linear-gradient(135deg,#c9cbc9,#6f7a80)"></div>
    <h3>Agile Project<br>Lifecycle Phases</h3>
  </article>
  <article class="card project-card" style="left:780px">
    <div class="photo" role="img" aria-label="Two managers walking through a warehouse" style="background:linear-gradient(135deg,#9fb2c2,#4f5d6b)"></div>
    <h3>Agile Project<br>Roles</h3>
  </article>

  <div class="round-arrow" style="left:18px;top:2679px"><svg width="18" height="14" viewBox="0 0 18 14"><path d="M16 7H2M7 2L2 7l5 5" stroke="#fff" stroke-width="2" fill="none"/></svg></div>
  <div class="round-arrow" style="left:1111px;top:2679px"><svg width="18" height="14" viewBox="0 0 18 14"><path d="M2 7h14M11 2l5 5-5 5" stroke="#fff" stroke-width="2" fill="none"/></svg></div>
</section>

<section class="contact">
  <svg class="abs" style="left:0;top:2978px" width="1200" height="60" viewBox="0 0 1200 60">
    <polygon points="0,0 1200,0 1200,60 0,60" fill="#fff"/>
    <polygon points="0,0 1200,0 1200,6 0,6" fill="var(--blue)"/>
    <polygon points="0,6 1141,40 1141,6 1200,6 1200,0 0,0" fill="var(--blue)"/>
    <polygon points="0,6 1141,36 1141,50 0,18" fill="var(--orange)"/>
  </svg>
  <div class="abs dot-field" role="img" aria-label="Dot grid decoration" style="left:873px;top:3085px;width:222px;height:160px"></div>
  <div class="abs dot-field" role="img" aria-label="Dot grid decoration" style="left:78px;top:3267px;width:310px;height:160px"></div>
  <div class="abs contact-orange">
    <small>CONTACT US</small>
    <strong>LET'S DO<br>GOOD<br>TOGETHER!</strong>
  </div>
  <form class="abs contact-form">
    <h2 class="abs heading" style="left:63px;top:38px;font-size:44px">Contact Us</h2>
    <div class="divider" style="left:63px;top:98px"><span></span><i></i><span></span></div>
    <div class="field" style="left:63px;top:136px"><label>YOUR NAME</label><span>Jordan Blakely</span></div>
    <div class="field" style="left:349px;top:136px"><label>COMPANY</label><span>jordan.blakely@example.com</span></div>
    <div class="field" style="left:63px;top:215px"><label>EMAIL ADDRESS</label><span>jordan.blakely@example.com</span></div>
    <div class="field" style="left:349px;top:215px"><label>PHONE</label><span>555 010 2234</span></div>
    <div class="field" style="left:63px;top:293px;width:463px;height:102px"><label>MESSAGE</label><span>Hi, do you have a moment to talk abo....</span></div>
    <div class="send"><svg width="30" height="30" viewBox="0 0 30 30"><path d="M27 3L3 13l10 4 4 10z" fill="#fff"/><path d="M27 3L13 17" stroke="var(--orange)" stroke-width="1.6"/></svg></div>
  </form>
</section>

<footer class="abs site-footer">
  <svg class="abs" style="left:0;top:-18px" width="1200" height="40" viewBox="0 0 1200 40">
    <polygon points="0,0 1200,0 1200,40 0,40" fill="var(--footer)"/>
    <polygon points="0,0 1200,0 1200,18 1141,18 1141,34 0,10" fill="#fff"/>
    <polygon points="0,4 1141,22 1141,34 0,14" fill="var(--orange)"/>
  </svg>
  <div class="brand footer-brand"><b></b><em>KEYSTONE DELIVERY</em></div>
  <div class="fcol" style="left:402px"><h4>Quick Links</h4><a href="#">Home</a><a href="#">Services</a><a href="#">Projects</a><a href="#">About us</a><a href="#">Articles</a></div>
  <div class="fcol" style="left:554px"><h4>Support</h4><a href="#">Team</a><a href="#">About Us</a><a href="#">Careers</a><a href="#">Our Values</a></div>
  <div class="fcol" style="left:694px"><h4>Links</h4><a href="#">Copyright</a><a href="#">Legal</a><a href="#">Privacy</a><a href="#">Accessibility</a><a href="#">Sitemap</a></div>
  <div class="fcol" style="left:836px;width:300px"><h4>Contact Us</h4>
    <div class="contact-row"><svg width="14" height="18" viewBox="0 0 14 18"><path d="M7 1a6 6 0 0 0-6 6c0 5 6 10 6 10s6-5 6-10a6 6 0 0 0-6-6z" fill="var(--blue)"/><circle cx="7" cy="7" r="2.2" fill="var(--footer)"/></svg><div><small>Address</small><span>Northgate Advisory Ltd, 14 Harbour Row<br>Riverside Quarter London, E3 4QT</span></div></div>
    <div class="contact-row"><svg width="14" height="14" viewBox="0 0 14 14"><path d="M3 1l3 3-2 2c1 2 2 3 4 4l2-2 3 3-2 2C6 13 1 8 1 3z" fill="var(--blue)"/></svg><div><small>Phone</small><span>+44 207 946 0321</span></div></div>
    <div class="contact-row"><svg width="14" height="12" viewBox="0 0 14 12"><rect x="1" y="1" width="12" height="10" fill="none" stroke="var(--blue)" stroke-width="1.5"/><path d="M1 1l6 5 6-5" fill="none" stroke="var(--blue)" stroke-width="1.5"/></svg><div><small>Email</small><span>hello@keystonedelivery.com</span></div></div>
  </div>
  <div class="abs footer-rule"></div>
  <div class="abs copyright">©2022. All rights reserved.</div>
  <div class="abs to-top"><svg width="14" height="10" viewBox="0 0 14 10"><path d="M2 8l5-5 5 5" stroke="#fff" stroke-width="2" fill="none"/></svg></div>
</footer>

</body>
</html>
```